Tech business card design

We need an amazing business card design for our new business 'Pexla' a marketing tech startup based in Sydney, Australia. We provide an online marketplace for businesses to search and buy advertising media, connect with service providers and learn more about marketing. We wish to communicate 'cool tech', reliability and professionalism and design based around our logo.

Target Market(s)

Business Owners

Contact Information for Business Card

Name
Position
Email Address
Website
Phone Number

Font styles to use
Other font styles liked:
• Avenir & Avenir Next

Colors

Designer to choose colors to be used in the design.

```html
<!DOCTYPE html>
<html lang="en">
<head>
<meta charset="utf-8">
<title>Pexla Business Card</title>
<link rel="stylesheet" href="https://fonts.googleapis.com/css2?family=Montserrat:wght@400;500;700;800&display=swap">
<style>
  :root {
    --backdrop: #2b2b2d;
    --paper: #ffffff;
    --navy: #0e1b4d;
    --navy-deep: #0a1540;
    --navy-soft: #1a2a62;
    --ink: #15204f;
    --muted: #5d6380;
    --rule: #d9dbe4;
    --light: #ffffff;
    --light-muted: #c3c8dc;
  }
  * { box-sizing: border-box; margin: 0; padding: 0; }
  html, body {
    width: 1200px; height: 907px; overflow: hidden;
    background: var(--backdrop);
    font-family: "Montserrat", sans-serif;
  }
  .stage {
    width: 1200px; height: 907px;
    display: flex; align-items: center; justify-content: center; gap: 48px;
  }
  .card {
    width: 520px; height: 300px; position: relative; overflow: hidden;
    box-shadow: 0 14px 30px rgba(0,0,0,0.45);
  }
  .card--front { background: var(--paper); }
  .card--back { background: var(--navy); }

  .wordmark {
    font-weight: 800; letter-spacing: -1px; line-height: 1;
    display: inline-flex; align-items: flex-start;
  }
  .wordmark__tm { font-size: 10px; font-weight: 800; margin-left: 4px; margin-top: 6px; letter-spacing: 0; }

  .card--front .wordmark {
    position: absolute; left: 34px; bottom: 56px;
    font-size: 76px; color: var(--ink);
  }
  .divider {
    position: absolute; left: 300px; top: 34px; width: 1px; height: 120px;
    background: var(--rule);
  }
  .contact {
    position: absolute; left: 318px; top: 38px; color: var(--ink);
  }
  .contact__name { font-size: 17px; font-weight: 700; letter-spacing: 0.5px; }
  .contact__role { font-size: 11px; color: var(--muted); margin-top: 3px; }
  .contact__list { list-style: none; margin-top: 18px; }
  .contact__item {
    display: flex; align-items: center; gap: 8px;
    font-size: 11px; color: var(--muted); margin-bottom: 5px;
  }
  .contact__icon { width: 11px; height: 11px; fill: var(--ink); flex: none; }

  .map-area {
    position: absolute; left: 60px; top: 30px; width: 400px; height: 220px;
    border-radius: 40% 45% 38% 50%;
    background: radial-gradient(ellipse at center, var(--navy-soft) 0%, var(--navy) 70%);
    opacity: 0.8;
  }
  .card--back .wordmark {
    position: absolute; left: 50%; top: 50%; transform: translate(-50%, -60%);
    font-size: 72px; color: var(--light);
  }
  .back__url {
    position: absolute; right: 40px; bottom: 46px;
    font-size: 12px; color: var(--light-muted); letter-spacing: 0.5px;
  }
</style>
</head>
<body>
<main class="stage">
  <section class="card card--front" aria-label="Card front">
    <div class="wordmark">pexla<span class="wordmark__tm">TM</span></div>
    <div class="divider"></div>
    <div class="contact">
      <p class="contact__name">MARCUS LANE</p>
      <p class="contact__role">Managing Director</p>
      <ul class="contact__list">
        <li class="contact__item">
          <svg class="contact__icon" viewBox="0 0 24 24" aria-hidden="true"><path d="M6.6 10.8a15.1 15.1 0 0 0 6.6 6.6l2.2-2.2c.3-.3.7-.4 1-.2 1.1.4 2.3.6 3.6.6.6 0 1 .4 1 1V20c0 .6-.4 1-1 1A17 17 0 0 1 3 4c0-.6.4-1 1-1h3.5c.6 0 1 .4 1 1 0 1.3.2 2.5.6 3.6.1.3 0 .7-.2 1z"/></svg>
          000-555-0142
        </li>
        <li class="contact__item">
          <svg class="contact__icon" viewBox="0 0 24 24" aria-hidden="true"><path d="M2 5h20v14H2z M2 5l10 8 10-8" fill="none" stroke="currentColor"/><path d="M2 5h20v2l-10 7L2 7z"/><path d="M2 8l10 7 10-7v11H2z"/></svg>
          info@pexlamail.com
        </li>
        <li class="contact__item">
          <svg class="contact__icon" viewBox="0 0 24 24" aria-hidden="true"><path d="M12 2a10 10 0 1 0 0 20 10 10 0 0 0 0-20zm6.9 6h-3a15.6 15.6 0 0 0-1.4-3.6A8 8 0 0 1 18.9 8zM12 4c.8 1.2 1.5 2.5 1.9 4h-3.8c.4-1.5 1.1-2.8 1.9-4zM4.3 14a8.2 8.2 0 0 1 0-4h3.4a16.5 16.5 0 0 0 0 4zm.8 2h3a15.6 15.6 0 0 0 1.4 3.6A8 8 0 0 1 5.1 16zm3-8h-3a8 8 0 0 1 4.4-3.6C8.9 5.5 8.4 6.7 8.1 8zM12 20c-.8-1.2-1.5-2.5-1.9-4h3.8c-.4 1.5-1.1 2.8-1.9 4zm2.3-6H9.7a14.7 14.7 0 0 1 0-4h4.6a14.7 14.7 0 0 1 0 4zm.2 5.6c.6-1.1 1.1-2.3 1.4-3.6h3a8 8 0 0 1-4.4 3.6zm1.8-5.6a16.5 16.5 0 0 0 0-4h3.4a8.2 8.2 0 0 1 0 4z"/></svg>
          www.pexla.com
        </li>
      </ul>
    </div>
  </section>

  <section class="card card--back" aria-label="Card back">
    <div class="map-area" role="img" aria-label="Faint dotted world map"></div>
    <div class="wordmark">pexla<span class="wordmark__tm">TM</span></div>
    <p class="back__url">www.pexla.com</p>
  </section>
</main>
</body>
</html>
```